Design a Website for an IT Support Company

We are an IT support company that provides commercial IT support and services to small and medium sized businesses. We are in need of a website to be developed for our business.
We would like to work with someone who is either familiar with the IT field, or has developed a website for an IT support company in the past.
Some examples of designs/layouts that we like:
https://www.veldaworks.example/
http://www.marsbyquill.example/
http://817kq.example/
http://www.olbenstructures.example/
http://www.bykq.example/
I have attached a word document that gives a menu system/page layout format that we would like for our website as well as branch office phone numbers. Our logo is also attached that you can use for your design purposes. We currently do not have copy produced for all of the pages outlined in the word document, but would get this done during the project with the selected designer.
We would like the website to be SEO friendly & fully responsive. We would prefer a Wordpress format, however, we are open to HTML formats as well.

```html
<!DOCTYPE html>
<html lang="en">
<head>
<meta charset="utf-8">
<title>Vantora IT — Managed IT Services</title>
<link href="https://fonts.googleapis.com/css2?family=Open+Sans:ital,wght@0,400;0,600;0,700;0,800;1,400&display=swap" rel="stylesheet">
<style>
:root{
  --blue:#1a74c6;
  --blue-dark:#145fa3;
  --ink:#2b2b2b;
  --text:#555;
  --dark:#2d2d2d;
  --darker:#222;
  --grey-bg:#f1f1f1;
  --card:#f4f4f4;
  --quote:#e2e2e2;
  --green:#3aa317;
  --white:#fff;
}
*{margin:0;padding:0;box-sizing:border-box}
html,body{width:1200px;height:3673px;overflow:hidden}
body{font-family:"Open Sans",Arial,sans-serif;color:var(--text);background:var(--white);position:relative}
.abs{position:absolute}
section,header,footer{position:absolute;left:0;width:1200px}

/* header */
.site-header{top:0;height:120px;background:var(--white)}
.brand{left:75px;top:18px;display:flex;align-items:center;gap:12px}
.brand-dot{width:34px;height:34px;border-radius:50%;background:var(--blue)}
.brand-name{font-size:34px;font-weight:700;color:var(--ink);letter-spacing:-.5px}
.header-cta{left:510px;top:18px;width:392px;height:40px;border:2px solid var(--green);color:var(--green);font-size:13px;font-weight:700;display:flex;align-items:center;justify-content:center;letter-spacing:.3px}
.header-phone{left:925px;top:18px;display:flex;align-items:center;gap:10px;font-size:25px;font-weight:600;color:var(--blue)}
.header-phone .ph{width:32px;height:32px;border-radius:50%;background:#777;display:flex;align-items:center;justify-content:center}
.main-nav{right:75px;top:84px;display:flex;gap:44px;font-size:14px;font-weight:700;color:var(--ink)}
.main-nav .active{color:var(--blue)}

/* hero */
.hero{top:120px;height:558px;background:linear-gradient(100deg,#3a5a78 0%,#9fb8cc 45%,#dfe7ee 70%,#c7d2da 100%)}
.hero-caption{left:75px;top:198px;width:552px;padding:14px 22px 18px;background:rgba(20,20,20,.85)}
.hero-caption h1{font-size:40px;font-weight:800;color:var(--white);line-height:1.1;letter-spacing:.5px}
.hero-caption h1 span{color:var(--blue)}
.hero-caption p{margin-top:8px;font-size:20px;font-weight:700;color:var(--white);line-height:1.4}
.hero-dots{left:0;right:0;top:520px;display:flex;justify-content:center;gap:8px}
.hero-dots i{width:10px;height:10px;border-radius:50%;background:rgba(255,255,255,.6)}
.hero-dots i:first-child{background:var(--blue)}

/* section titles */
.section-title{left:0;width:1200px;text-align:center;font-size:26px;font-weight:700;color:var(--ink);letter-spacing:.5px}

/* services */
.services{top:678px;height:487px}
.service-card{top:97px;width:330px;height:338px;background:var(--card);box-shadow:0 6px 10px rgba(0,0,0,.12);padding:28px 26px}
.service-head{display:flex;align-items:center;gap:22px;height:60px}
.service-head h3{font-size:23px;font-weight:700;color:var(--blue)}
.service-list{list-style:none;margin-top:16px}
.service-list li{font-size:15px;color:var(--text);line-height:29.5px;display:flex;align-items:center;gap:14px;white-space:nowrap}
.service-list li svg{flex:none}
.btn-small{display:inline-block;margin-top:14px;background:var(--blue);color:var(--white);font-size:12px;font-weight:700;padding:9px 12px}

/* welcome */
.welcome{top:1165px;height:365px;background:var(--dark)}
.welcome-photo{left:0;top:0;width:580px;height:365px;background:linear-gradient(120deg,#c9d2da,#8e99a3 55%,#e1e6ea)}
.welcome-text{left:640px;top:70px;width:500px}
.welcome-text h2{font-size:25px;font-weight:700;color:var(--white);letter-spacing:.5px}
.welcome-text p{margin-top:18px;font-size:15px;line-height:27px;color:#d6d6d6}
.btn-blue{display:inline-block;margin-top:22px;background:var(--blue);color:var(--white);font-size:14px;font-weight:700;padding:16px 32px}

/* why */
.why{top:1530px;height:820px;background:var(--blue)}
.why .section-title{color:var(--white);top:50px}
.video-frame{left:288px;top:110px;width:624px;height:365px;border:5px solid #5ea8e6}
.video-still{width:100%;height:100%;background:linear-gradient(120deg,#7f9a86 0%,#c9d3cf 45%,#e8ecee 65%,#8aa08c 100%)}
.play{left:280px;top:150px;width:56px;height:56px;border-radius:50%;background:rgba(40,40,40,.75);border:3px solid var(--white);display:flex;align-items:center;justify-content:center}
.features{left:75px;top:520px;width:1050px;display:flex}
.feature{flex:1;text-align:center;padding:0 30px;border-right:1px solid rgba(255,255,255,.25)}
.feature:last-child{border-right:0}
.feature-icon{width:84px;height:84px;margin:0 auto;border-radius:50%;background:var(--darker);border:3px solid var(--white);display:flex;align-items:center;justify-content:center}
.feature h3{margin-top:26px;font-size:16px;font-weight:700;color:var(--white);line-height:22px}
.feature p{margin-top:8px;font-size:14px;color:#e6f0fa;line-height:21px}
.why-arrow{top:620px}

/* testimonials */
.testimonials{top:2350px;height:440px}
.testimonial{top:100px;width:330px;height:200px;background:var(--card);padding:22px 26px;text-align:center}
.testimonial p,.testimonial .who{position:relative;z-index:1}
.testimonial p{font-size:13.5px;font-style:italic;color:#777;line-height:23px}
.testimonial .who{margin-top:12px;font-size:13px;font-weight:700;color:var(--blue)}
.quote{z-index:0;font-size:80px;font-weight:800;color:var(--quote);line-height:1}
.avatar{width:72px;height:72px;border-radius:50%;background:linear-gradient(#d9d9d9,#9a9a9a);border:3px solid var(--white)}
.slider-dots{left:0;width:1200px;top:380px;display:flex;justify-content:center;gap:6px}
.slider-dots i{width:13px;height:13px;border-radius:50%;background:#555}
.slider-dots i:first-child{background:var(--blue)}

/* partners */
.partners{top:2790px;height:195px;background:var(--grey-bg)}
.partner-row{left:75px;top:98px;width:1050px;display:flex;justify-content:space-between;align-items:center}
.partner-badge{height:50px;background:#b9c0c8;border-radius:4px}

/* schedule */
.schedule{top:2985px;height:345px;background:var(--dark)}
.schedule .section-title{color:var(--white);top:58px;font-size:25px}
.field{width:332px;height:42px;background:var(--white);font-size:13px;color:#444;padding:0 14px;display:flex;align-items:center}
.btn-green{left:497px;top:240px;width:208px;height:50px;background:var(--green);color:var(--white);font-size:14px;font-weight:700;display:flex;align-items:center;justify-content:center}

/* footer */
.site-footer{top:3330px;height:280px;background:var(--blue)}
.foot-brand{left:75px;top:50px;display:flex;align-items:center;gap:10px}
.foot-brand .brand-dot{background:var(--white);width:28px;height:28px}
.foot-brand .brand-name{color:var(--white);font-size:28px}
.offices{left:75px;top:128px;font-size:12.5px;color:var(--white);line-height:21.5px;border-collapse:collapse}
.offices td:first-child{width:102px}
.foot-col h4{font-size:12.5px;font-weight:700;color:var(--white);letter-spacing:.3px}
.sitemap{left:368px;top:50px}
.sitemap ul{list-style:none;margin-top:14px;font-size:12.5px;color:var(--white);line-height:31px}
.blog{left:534px;top:50px;width:300px}
.post{display:flex;gap:18px;margin-top:16px}
.post-thumb{width:75px;height:55px;flex:none;background:linear-gradient(135deg,#e8ecef,#9fb3c4)}
.post b{display:block;font-size:12.5px;color:var(--white);font-weight:700}
.post span{display:block;font-size:12px;color:#e0ecf8;line-height:18px;margin-top:2px}
.signup{left:885px;top:50px;width:240px}
.signup .field{margin-top:18px;width:240px;height:42px;font-size:12px;color:#777}
.signup-btn{margin:14px 0 0 auto;width:92px;height:42px;background:#111;color:var(--white);font-size:12.5px;font-weight:700;display:flex;align-items:center;justify-content:center}
.bottom-bar{top:3610px;height:63px;background:var(--darker)}
.copyright{left:75px;top:24px;font-size:11px;color:#999}
.social{right:75px;top:22px;display:flex;gap:16px}
.social i{width:18px;height:18px;background:#e4e4e4;border-radius:2px}
</style>
</head>
<body>

<header class="site-header">
  <div class="abs brand"><span class="brand-dot"></span><span class="brand-name">Vantora IT</span></div>
  <div class="abs header-cta">SCHEDULE A FREE NETWORK ASSESSMENT TODAY!</div>
  <div class="abs header-phone">
    <span class="ph"><svg width="16" height="16" viewBox="0 0 24 24"><path fill="#fff" d="M6.6 10.8c1.4 2.8 3.8 5.1 6.6 6.6l2.2-2.2c.3-.3.7-.4 1-.2 1.1.4 2.3.6 3.6.6.6 0 1 .4 1 1V20c0 .6-.4 1-1 1C10.6 21 3 13.4 3 4c0-.6.4-1 1-1h3.5c.6 0 1 .4 1 1 0 1.3.2 2.5.6 3.6.1.3 0 .7-.2 1z"/></svg></span>
    555-014-2200
  </div>
  <nav class="abs main-nav"><span class="active">HOME</span><span>DATA</span><span>CLOUD</span><span>VOICE</span><span>CONTACT</span></nav>
</header>

<section class="hero" role="img" aria-label="Professional using a laptop in front of server racks with floating interface tiles">
  <div class="abs hero-caption">
    <h1>IT MANAGED <span>SERVICES</span></h1>
    <p>We are an IT support company that provides commercial IT support and services to small and medium sized businesse.</p>
  </div>
  <div class="abs hero-dots"><i></i><i></i><i></i></div>
</section>

<section class="services">
  <h2 class="abs section-title" style="top:44px">OUR SERVICES</h2>

  <article class="abs service-card" style="left:75px">
    <div class="service-head">
      <svg width="48" height="56" viewBox="0 0 48 56"><g fill="#2b2b2b"><ellipse cx="24" cy="8" rx="22" ry="7"/><path d="M2 14c0 4 10 7 22 7s22-3 22-7v10c0 4-10 7-22 7S2 28 2 24z"/><path d="M2 30c0 4 10 7 22 7s22-3 22-7v10c0 4-10 7-22 7S2 44 2 40z"/></g></svg>
      <h3>DATA</h3>
    </div>
    <ul class="service-list">
      <li><svg width="12" height="10" viewBox="0 0 12 10"><path d="M1 5l3.5 3.5L11 1.5" stroke="#1a74c6" stroke-width="2.4" fill="none"/></svg>Managed IT Services</li>
      <li><svg width="12" height="10" viewBox="0 0 12 10"><path d="M1 5l3.5 3.5L11 1.5" stroke="#1a74c6" stroke-width="2.4" fill="none"/></svg>IT Support &amp; Consulting</li>
      <li><svg width="12" height="10" viewBox="0 0 12 10"><path d="M1 5l3.5 3.5L11 1.5" stroke="#1a74c6" stroke-width="2.4" fill="none"/></svg>IT Helpdesk Services</li>
      <li><svg width="12" height="10" viewBox="0 0 12 10"><path d="M1 5l3.5 3.5L11 1.5" stroke="#1a74c6" stroke-width="2.4" fill="none"/></svg>Network Security</li>
      <li><svg width="12" height="10" viewBox="0 0 12 10"><path d="M1 5l3.5 3.5L11 1.5" stroke="#1a74c6" stroke-width="2.4" fill="none"/></svg>Data Backup &amp; Recovery</li>
    </ul>
    <span class="btn-small">READ MORE</span>
  </article>

  <article class="abs service-card" style="left:435px">
    <div class="service-head">
      <svg width="64" height="44" viewBox="0 0 64 44"><path fill="#2b2b2b" d="M14 44C6 44 0 38 0 31c0-6 4-11 10-12 1-10 9-18 20-18 8 0 15 5 18 12 1 0 2 0 3 0 7 0 13 6 13 14s-6 17-14 17z"/></svg>
      <h3>CLOUD</h3>
    </div>
    <ul class="service-list">
      <li><svg width="12" height="10" viewBox="0 0 12 10"><path d="M1 5l3.5 3.5L11 1.5" stroke="#1a74c6" stroke-width="2.4" fill="none"/></svg>Cloud Office Suite Migrations</li>
      <li><svg width="12" height="10" viewBox="0 0 12 10"><path d="M1 5l3.5 3.5L11 1.5" stroke="#1a74c6" stroke-width="2.4" fill="none"/></svg>Northcloud Management Services</li>
      <li><svg width="12" height="10" viewBox="0 0 12 10"><path d="M1 5l3.5 3.5L11 1.5" stroke="#1a74c6" stroke-width="2.4" fill="none"/></svg>Cloud Migration Services</li>
      <li><svg width="12" height="10" viewBox="0 0 12 10"><path d="M1 5l3.5 3.5L11 1.5" stroke="#1a74c6" stroke-width="2.4" fill="none"/></svg>Hosted Virtual Servers</li>
      <li><svg width="12" height="10" viewBox="0 0 12 10"><path d="M1 5l3.5 3.5L11 1.5" stroke="#1a74c6" stroke-width="2.4" fill="none"/></svg>Hosted Telephone Systems</li>
    </ul>
    <span class="btn-small">READ MORE</span>
  </article>

  <article class="abs service-card" style="left:795px">
    <div class="service-head">
      <svg width="48" height="48" viewBox="0 0 24 24"><path fill="#2b2b2b" d="M6.6 10.8c1.4 2.8 3.8 5.1 6.6 6.6l2.2-2.2c.3-.3.7-.4 1-.2 1.1.4 2.3.6 3.6.6.6 0 1 .4 1 1V20c0 .6-.4 1-1 1C10.6 21 3 13.4 3 4c0-.6.4-1 1-1h3.5c.6 0 1 .4 1 1 0 1.3.2 2.5.6 3.6.1.3 0 .7-.2 1z"/></svg>
      <h3>VOICE</h3>
    </div>
    <ul class="service-list">
      <li><svg width="12" height="10" viewBox="0 0 12 10"><path d="M1 5l3.5 3.5L11 1.5" stroke="#1a74c6" stroke-width="2.4" fill="none"/></svg>Starline PBX Consulting</li>
      <li><svg width="12" height="10" viewBox="0 0 12 10"><path d="M1 5l3.5 3.5L11 1.5" stroke="#1a74c6" stroke-width="2.4" fill="none"/></svg>Business Telephone Systems</li>
      <li><svg width="12" height="10" viewBox="0 0 12 10"><path d="M1 5l3.5 3.5L11 1.5" stroke="#1a74c6" stroke-width="2.4" fill="none"/></svg>Multiple Office Phone Systems</li>
      <li><svg width="12" height="10" viewBox="0 0 12 10"><path d="M1 5l3.5 3.5L11 1.5" stroke="#1a74c6" stroke-width="2.4" fill="none"/></svg>Halvane Telephone Systems</li>
      <li><svg width="12" height="10" viewBox="0 0 12 10"><path d="M1 5l3.5 3.5L11 1.5" stroke="#1a74c6" stroke-width="2.4" fill="none"/></svg>SIP Trunks</li>
    </ul>
    <span class="btn-small">READ MORE</span>
  </article>
</section>

<section class="welcome">
  <div class="abs welcome-photo" role="img" aria-label="Support team wearing headsets working at computers in a bright office"></div>
  <div class="abs welcome-text">
    <h2>WELCOME TO OUR WEBSITE</h2>
    <p>Technology is the backbone of your business. Vantora IT excels at providing outsourced network IT support to businesses just like yours. Our team of friendly and highly experienced engineers are standing by to help you get the most out of your technology.</p>
    <span class="btn-blue">READ MORE</span>
  </div>
</section>

<section class="why">
  <h2 class="abs section-title">WHY VANTORA IT</h2>
  <div class="abs video-frame">
    <div class="video-still" role="img" aria-label="Video still: support agent with a headset shown on a tablet"></div>
    <div class="abs play"><svg width="18" height="22" viewBox="0 0 18 22"><path d="M2 1l15 10L2 21z" fill="#fff"/></svg></div>
  </div>
  <svg class="abs why-arrow" style="left:44px" width="14" height="22" viewBox="0 0 14 22"><path d="M11 2L3 11l8 9" stroke="#fff" stroke-width="3" fill="none"/></svg>
  <svg class="abs why-arrow" style="left:1142px" width="14" height="22" viewBox="0 0 14 22"><path d="M3 2l8 9-8 9" stroke="#fff" stroke-width="3" fill="none"/></svg>
  <div class="abs features">
    <div class="feature">
      <div class="feature-icon"><svg width="34" height="30" viewBox="0 0 34 30"><g fill="none" stroke="#fff" stroke-width="3"><circle cx="12" cy="17" r="6"/><circle cx="26" cy="8" r="4"/></g><g fill="#fff"><rect x="10" y="6" width="4" height="4"/><rect x="10" y="24" width="4" height="4"/><rect x="1" y="15" width="4" height="4"/><rect x="19" y="15" width="4" height="4"/></g></svg></div>
      <h3>Control IT Spending</h3>
      <p>We offer an all-inclusive proactive, reliable, and affordable solution for your IT support needs..</p>
    </div>
    <div class="feature">
      <div class="feature-icon"><svg width="32" height="28" viewBox="0 0 32 28"><path d="M2 2v24h28" stroke="#fff" stroke-width="3" fill="none"/><path d="M7 20l7-8 5 5 9-10" stroke="#fff" stroke-width="3" fill="none"/></svg></div>
      <h3>Optimized IT Efficiency</h3>
      <p>Technology is not a one size fits all approach. Vantora IT determines and implements solutions...</p>
    </div>
    <div class="feature">
      <div class="feature-icon"><svg width="32" height="28" viewBox="0 0 32 28"><g fill="#fff"><rect x="12" y="1" width="8" height="7"/><rect x="1" y="20" width="8" height="7"/><rect x="12" y="20" width="8" height="7"/><rect x="23" y="20" width="8" height="7"/></g><path d="M16 8v12M5 20v-6h22v6" stroke="#fff" stroke-width="2" fill="none"/></svg></div>
      <h3>Real Proactive Network Management</h3>
      <p>Our approach to IT support and network management is based upon a proven checklist..</p>
    </div>
  </div>
</section>

<section class="testimonials">
  <h2 class="abs section-title" style="top:38px">CUSTOMER TESTIMONIALS</h2>
  <div class="abs testimonial" style="left:75px">
    <span class="abs quote" style="left:8px;top:4px">“</span>
    <p>Aliquam molestie, mi et imperdiet euismod, dui purus auctor tellus, et interdum lacus lectus et ante. Sed accumsan sollicitudin sapien, sit amet adipiscing turpis...</p>
    <div class="who">-NAME HEADING</div>
    <span class="abs quote" style="right:8px;bottom:-26px">”</span>
  </div>
  <div class="abs avatar" style="left:204px;top:262px" role="img" aria-label="Client portrait"></div>
  <div class="abs testimonial" style="left:435px">
    <span class="abs quote" style="left:8px;top:4px">“</span>
    <p>Aliquam molestie, mi et imperdiet euismod, dui purus auctor tellus, et interdum lacus lectus et ante. Sed accumsan sollicitudin sapien, sit amet adipiscing turpis...</p>
    <div class="who">-NAME HEADING</div>
    <span class="abs quote" style="right:8px;bottom:-26px">”</span>
  </div>
  <div class="abs avatar" style="left:564px;top:262px" role="img" aria-label="Client portrait"></div>
  <div class="abs testimonial" style="left:795px">
    <span class="abs quote" style="left:8px;top:4px">“</span>
    <p>Aliquam molestie, mi et imperdiet euismod, dui purus auctor tellus, et interdum lacus lectus et ante. Sed accumsan sollicitudin sapien, sit amet adipiscing turpis...</p>
    <div class="who">-NAME HEADING</div>
    <span class="abs quote" style="right:8px;bottom:-26px">”</span>
  </div>
  <div class="abs avatar" style="left:924px;top:262px" role="img" aria-label="Client portrait"></div>
  <div class="abs slider-dots"><i></i><i></i><i></i></div>
</section>

<section class="partners">
  <h2 class="abs section-title" style="top:40px;font-size:25px">OUR PARTNERS</h2>
  <div class="abs partner-row">
    <span class="partner-badge" style="width:92px" role="img" aria-label="Partner badge"></span>
    <span class="partner-badge" style="width:140px" role="img" aria-label="Partner badge"></span>
    <span class="partner-badge" style="width:110px" role="img" aria-label="Partner badge"></span>
    <span class="partner-badge" style="width:225px" role="img" aria-label="Partner badge"></span>
    <span class="partner-badge" style="width:180px" role="img" aria-label="Partner badge"></span>
    <span class="partner-badge" style="width:100px" role="img" aria-label="Partner badge"></span>
  </div>
</section>

<section class="schedule">
  <h2 class="abs section-title">SCHEDULE A FREE NETWORK ASSESSMENT TODAY</h2>
  <div class="abs field" style="left:255px;top:120px">Name</div>
  <div class="abs field" style="left:615px;top:120px">Company Name</div>
  <div class="abs field" style="left:255px;top:175px">Email Address</div>
  <div class="abs field" style="left:615px;top:175px">Phone No.</div>
  <div class="abs btn-green">SCHEDULE NOW</div>
</section>

<footer class="site-footer">
  <div class="abs foot-brand"><span class="brand-dot"></span><span class="brand-name">Vantora IT</span></div>
  <table class="abs offices">
    <tr><td>Main Number:</td><td>555-014-2200</td></tr>
    <tr><td>Houston:</td><td>555-014-2301</td></tr>
    <tr><td>San Antonio:</td><td>555-014-2402</td></tr>
    <tr><td>Austin:</td><td>555-014-2503</td></tr>
    <tr><td>Tulsa:</td><td>555-014-2604</td></tr>
    <tr><td>Oklahoma City:</td><td>555-014-2705</td></tr>
  </table>
  <div class="abs foot-col sitemap">
    <h4>SITE MAP</h4>
    <ul><li>Home</li><li>Services</li><li>Why Vantora IT</li><li>Contact us</li></ul>
  </div>
  <div class="abs foot-col blog">
    <h4>BLOG POSTS</h4>
    <div class="post"><div class="post-thumb" role="img" aria-label="Blog post thumbnail"></div><div><b>Consectetuer adipiscing elit</b><span>Aenean a nibh eget turpis vehicula tempus ac...</span></div></div>
    <div class="post"><div class="post-thumb" role="img" aria-label="Blog post thumbnail"></div><div><b>Consectetuer adipiscing elit</b><span>Aenean a nibh eget turpis vehicula tempus ac...</span></div></div>
  </div>
  <div class="abs foot-col signup">
    <h4>EMAIL SIGN UP</h4>
    <div class="field">Enter Email Address</div>
    <div class="signup-btn">SIGN UP</div>
  </div>
</footer>

<div class="abs bottom-bar" style="left:0;width:1200px">
  <div class="abs copyright">Copyright © 2017, Company Name. All Right Reserved</div>
  <div class="abs social"><i aria-label="Social link"></i><i aria-label="Social link"></i><i aria-label="Social link"></i><i aria-label="Social link"></i><i aria-label="Social link"></i></div>
</div>

</body>
</html>
```